Veltrane Group Business Card Design

The CEO is looking for a new trendy look for his business card.
You can stay with current branding or come up with something new/creative. It can be 3D, including Medical Office buildings. You can use our logo in a variety of colors. Please include name, title, company name, company website, email address, cell number

Target Market(s)

Real Estate Development and Construction

Industry/Entity Type

Health care real estate

Contact Information for Business Card

Rohesh Kamdar, CEO M-604.781.2249 E-roheshkamdar@veltrane.com Address:4180 Lindqvist Ave, Tampa, FL 33482 www.veltrane.com

Font styles to use
Other font styles liked:
• Be creative

Requirements
Must have
• Creative, trendy look
Nice to have
• Please go to our website to get a feel- www. veltrane.com
Should not have
• small fonts

```html
<!DOCTYPE html>
<html lang="en">
<head>
<meta charset="utf-8">
<title>Veltrane Group Business Card</title>
<link href="https://fonts.googleapis.com/css2?family=Montserrat:wght@400;700;800&display=swap" rel="stylesheet">
<style>
  :root {
    --stage: #2b2d31;
    --card-black: #0e0e0f;
    --card-white: #ffffff;
    --text-light: #e9e9e9;
    --text-muted: #b8b8b8;
  }
  * { margin: 0; padding: 0; box-sizing: border-box; }
  html, body {
    width: 1200px; height: 900px; overflow: hidden;
    background: var(--stage);
    font-family: "Montserrat", sans-serif;
  }
  .stage { position: relative; width: 1200px; height: 900px; }

  .card {
    position: absolute;
    border-radius: 26px;
    background: var(--card-black);
    overflow: hidden;
    box-shadow: 0 18px 40px rgba(0,0,0,.45);
  }

  /* Front: portrait */
  .card-front { left: 150px; top: 188px; width: 300px; height: 525px; }
  .card-front .shape { position: absolute; inset: 0; }
  .contact { position: relative; z-index: 1; padding: 34px 0 0 30px; color: var(--text-light); }
  .contact .name { font-weight: 700; font-size: 19px; letter-spacing: .2px; }
  .contact .title { font-size: 10px; color: var(--text-muted); margin-top: 3px; letter-spacing: 1px; }
  .contact .address { font-size: 11px; line-height: 1.45; margin-top: 26px; color: var(--text-muted); }
  .contact ul { list-style: none; margin-top: 14px; }
  .contact li { display: flex; align-items: center; gap: 8px; font-size: 11px; margin-bottom: 6px; color: var(--text-light); white-space: nowrap; }
  .contact li svg { width: 11px; height: 11px; flex: none; }

  .front-mark {
    position: absolute; left: 0; right: 0; top: 355px;
    text-align: center; color: var(--card-black);
    font-weight: 800; font-size: 34px; line-height: .95; letter-spacing: -1px;
  }
  .front-mark span { display: block; font-size: 24px; letter-spacing: 0; }

  /* Back: landscape */
  .card-back { left: 530px; top: 300px; width: 525px; height: 300px; }
  .back-mark {
    position: absolute; left: 0; right: 0; top: 82px;
    text-align: center; color: var(--card-white);
    font-weight: 800; font-size: 72px; line-height: .9; letter-spacing: -2px;
  }
  .back-mark span { display: block; font-size: 46px; letter-spacing: 0; padding-left: 170px; }
</style>
</head>
<body>
<main class="stage">

  <section class="card card-front">
    <svg class="shape" viewBox="0 0 300 525" preserveAspectRatio="none" aria-hidden="true">
      <path d="M0 525 L0 475 C20 340 110 262 200 260 C265 259 300 300 300 340 L300 525 Z" fill="var(--card-white)"/>
      <path d="M-5 440 C20 310 110 242 205 242 C268 242 300 278 306 310" fill="none" stroke="var(--card-white)" stroke-width="4"/>
    </svg>

    <div class="contact">
      <div class="name">Rohesh Kamdar</div>
      <div class="title">CEO</div>
      <div class="address">4180 Lindqvist Ave,<br>Tampa, FL 33482</div>
      <ul>
        <li>
          <svg viewBox="0 0 12 12"><path d="M2.5 1h2l1 3-1.4 1a6 6 0 0 0 2.9 2.9L8 6.5l3 1v2A1.5 1.5 0 0 1 9.5 11 8.5 8.5 0 0 1 1 2.5 1.5 1.5 0 0 1 2.5 1z" fill="currentColor"/></svg>
          604.781.2249
        </li>
        <li>
          <svg viewBox="0 0 12 12"><rect x="1" y="2.5" width="10" height="7" rx="1" fill="currentColor"/><path d="M1.5 3l4.5 3.5L10.5 3" fill="none" stroke="var(--card-black)" stroke-width="1"/></svg>
          roheshkamdar@veltrane.com
        </li>
        <li>
          <svg viewBox="0 0 12 12"><circle cx="6" cy="6" r="4.8" fill="none" stroke="currentColor" stroke-width="1.2"/><ellipse cx="6" cy="6" rx="2" ry="4.8" fill="none" stroke="currentColor" stroke-width="1"/><path d="M1.2 6h9.6" stroke="currentColor" stroke-width="1"/></svg>
          www.veltrane.com
        </li>
      </ul>
    </div>

    <div class="front-mark">Veltrane<span>group</span></div>
  </section>

  <section class="card card-back">
    <div class="back-mark">Veltrane<span>group</span></div>
  </section>

</main>
</body>
</html>
```